Album Cover Art for New Single

Independent singer-songwriter and pianist, seeking design work for a new single "Walk Beside the Lantern". Christian & Gospel music format. See attached for master recording.

This single is personal for me, so I'm looking for an image that really captures the heart of the message. Redemption, forgiveness, prodigals returning home to a loving father.
Updates

Target Market(s)

Millenials

Colors

Designer to choose colors to be used in the design.

Requirements
Must have
• simple graphic, must include the following text:
• Walk Beside the Lantern
• Dale Verrick
Should not have
• Avoid "cheesy" look and feel.

```html
<!DOCTYPE html>
<html lang="en">
<head>
<meta charset="utf-8">
<title>Walk Beside the Lantern — Dale Verrick</title>
<link rel="stylesheet" href="https://fonts.googleapis.com/css2?family=Permanent+Marker&family=Cormorant+Garamond:wght@600&display=block">
<style>
  :root {
    --fog-top: #ececec;
    --fog-mid: #d6d6d6;
    --tree-line: #bdbdbd;
    --ground-light: #8e8e8e;
    --ground-dark: #5a5a5a;
    --ground-deep: #3a3a3a;
    --ink-light: #ffffff;
  }
  html, body {
    margin: 0;
    padding: 0;
    width: 1200px;
    height: 1200px;
    overflow: hidden;
    background: var(--fog-top);
  }
  .cover {
    position: relative;
    width: 1200px;
    height: 1200px;
    overflow: hidden;
  }
  .cover-photo {
    position: absolute;
    inset: 0;
    background:
      radial-gradient(ellipse 260px 560px at 345px 720px, rgba(40,40,40,0.55), rgba(40,40,40,0) 100%),
      radial-gradient(ellipse 900px 260px at 600px 420px, rgba(175,175,175,0.55), rgba(175,175,175,0) 100%),
      linear-gradient(180deg,
        var(--fog-top) 0%,
        var(--fog-top) 18%,
        var(--fog-mid) 30%,
        var(--tree-line) 40%,
        var(--ground-light) 50%,
        #767676 62%,
        var(--ground-dark) 80%,
        var(--ground-deep) 100%);
  }
  .single-title {
    position: absolute;
    top: 372px;
    right: 96px;
    margin: 0;
    font-family: "Permanent Marker", "Marker Felt", "Comic Sans MS", cursive;
    font-weight: 400;
    font-size: 150px;
    line-height: 152px;
    text-align: right;
    text-transform: uppercase;
    color: var(--ink-light);
    letter-spacing: 1px;
  }
  .single-title span {
    display: block;
    white-space: nowrap;
  }
  .artist-name {
    position: absolute;
    left: 0;
    width: 1200px;
    top: 1108px;
    margin: 0;
    text-align: center;
    font-family: "Cormorant Garamond", serif;
    font-weight: 600;
    font-size: 28px;
    line-height: 34px;
    letter-spacing: 11px;
    text-transform: uppercase;
    color: var(--ink-light);
  }
</style>
</head>
<body>
  <main class="cover">
    <div class="cover-photo" role="img" aria-label="Black and white photograph of a man in a hooded puffer jacket walking away along a narrow path through wild grass toward a foggy pine forest"></div>
    <h1 class="single-title">
      <span>Walk</span>
      <span>Beside</span>
      <span>The</span>
      <span>Lantern</span>
    </h1>
    <p class="artist-name">Dale Verrick</p>
  </main>
</body>
</html>
```